Larkspur Talent IT Recruiting firm needs a business card design for Recruiters, Sourcers, and Account

We need business cards that allow us to change all contact info, names, titles (Recruiter, Sourcer, Account Manager, Director, CEO, etc) per person since we have three offices, in three cities, Phoenix, Austin, and Las Vegas. We do recruiting and contractors for IT positions (Developers, Architects, Software Engineers, Security Engineers, Help Desk, DBAs, PMs, Scrum Masters, etc.) Our client companies are very diverse from Meridian 100 to silicone Valley type start-ups.

So, while we what hip, techie, and quirky, it still needs to be professional. Primary color we use is blue, with silver as a secondary color.

Target Market(s)

IT, Technology

Industry/Entity Type

Business

Contact Information for Business Card

Company name: Larkspur Talent, Inc.
Website: www.larkspurtalent.example
Logos for Careerloop, Blipster, and Myriada

Name, Title, Office Number, Cell Number, email

Font styles to use
Serif
Sans Serif

Colors
0455a3
d5d5d5

Requirements
Nice to have
• The grey I selected below is not necessary - but, would like silver included. I included a card design (File 3: LTI early trial example.jpg) that I had started on. It's very rough, and not quite what we're looking for, but what we did like is the logo, big, maybe a bit faded, off center, goes out of frame, etc. Still looking for other ideas - you are the pros! But, just an idea of a design element we liked.

```html
<!DOCTYPE html>
<html lang="en">
<head>
<meta charset="utf-8">
<title>Larkspur Talent – Business Card</title>
<link rel="stylesheet" href="https://fonts.googleapis.com/css2?family=Marcellus&family=PT+Sans:wght@400&display=swap">
<style>
  :root {
    --stage: #1c1c1c;
    --brand-blue: #0455a3;
    --brand-blue-light: #0a86cf;
    --brand-blue-mid: #1373c4;
    --ink: #2a2a2a;
    --paper: #ffffff;
    --back-grey: #575757;
    --silver: #d5d5d5;
    --silver-faint: #6a6a6a;
  }
  * { box-sizing: border-box; margin: 0; padding: 0; }
  html, body { width: 1200px; height: 907px; overflow: hidden; background: var(--stage); }
  .stage { position: relative; width: 1200px; height: 907px; }

  .card { position: absolute; left: 300px; width: 600px; height: 343px; overflow: hidden; }
  .card--front { top: 98px; background: var(--paper); }
  .card--back { top: 475px; background: var(--back-grey); }

  .front-wave { position: absolute; inset: 0; }

  .wordmark { position: absolute; font-family: "Marcellus", serif; line-height: 1; display: flex; flex-direction: column; }
  .wordmark__lockup { display: flex; flex-direction: column; align-items: flex-end; }
  .wordmark__name { display: flex; align-items: center; gap: 10px; letter-spacing: 3px; }
  .wordmark__sub { letter-spacing: 4px; margin-top: 2px; }
  .wordmark__dot { border-radius: 50%; flex: none; }
  .wordmark__tagline { letter-spacing: 1.6px; white-space: nowrap; }

  .card--front .wordmark { left: 0; right: 0; top: 42px; align-items: center; }
  .card--front .wordmark__name { font-size: 40px; color: var(--ink); }
  .card--front .wordmark__dot { width: 28px; height: 28px; background: var(--brand-blue); }
  .card--front .wordmark__sub { font-size: 27px; color: var(--brand-blue-mid); }
  .card--front .wordmark__tagline { font-size: 14px; color: var(--ink); margin-top: 16px; }

  .person { position: absolute; right: 371px; top: 238px; text-align: right; font-family: "PT Sans", sans-serif; color: #fff; }
  .person__name { font-size: 22px; line-height: 1.1; }
  .person__title { font-size: 15px; margin-top: 5px; }
  .divider { position: absolute; left: 246px; top: 224px; width: 1px; height: 76px; background: rgba(255,255,255,0.6); }

  .contacts { position: absolute; left: 270px; top: 219px; list-style: none; font-family: "PT Sans", sans-serif; font-size: 15px; color: #fff; }
  .contacts li { display: flex; align-items: center; height: 22.7px; }
  .contacts svg { width: 14px; height: 14px; margin-right: 6px; flex: none; }

  .emblem-fade { position: absolute; left: 4px; top: 4px; width: 336px; height: 336px; border-radius: 50%;
    background: radial-gradient(circle at 50% 40%, #767676, var(--silver-faint) 70%, #5f5f5f); }

  .social { position: absolute; right: 36px; top: 40px; display: flex; gap: 10px; list-style: none;
    font-family: "PT Sans", sans-serif; font-size: 12px; color: var(--silver); }
  .social li { display: flex; align-items: center; gap: 4px; }
  .social li::before { content: ""; width: 10px; height: 10px; background: var(--silver); }

  .card--back .wordmark { right: 34px; top: 236px; align-items: flex-end; }
  .card--back .wordmark__name { font-size: 32px; color: #fff; }
  .card--back .wordmark__dot { width: 22px; height: 22px; background: #fff; }
  .card--back .wordmark__sub { font-size: 22px; color: #fff; }
  .card--back .wordmark__tagline { font-size: 12.5px; color: #fff; margin-top: 8px; }
</style>
</head>
<body>
<main class="stage">

  <section class="card card--front" aria-label="Card front">
    <svg class="front-wave" viewBox="0 0 600 343" width="600" height="343" aria-hidden="true">
      <defs>
        <radialGradient id="bandGlow" cx="0.6" cy="0.95" r="0.8">
          <stop offset="0" stop-color="var(--brand-blue-light)"/>
          <stop offset="1" stop-color="var(--brand-blue)"/>
        </radialGradient>
      </defs>
      <path d="M0,168 Q300,214 600,158 L600,343 L0,343 Z" fill="url(#bandGlow)"/>
      <path d="M0,172 Q300,212 600,164" fill="none" stroke="#fff" stroke-width="3"/>
    </svg>

    <div class="wordmark">
      <div class="wordmark__lockup">
        <div class="wordmark__name"><span class="wordmark__dot"></span>LARKSPUR</div>
        <div class="wordmark__sub">TALENT</div>
      </div>
      <div class="wordmark__tagline">RECRUITING BRIGHT MINDS</div>
    </div>

    <div class="person">
      <div class="person__name">Dana Whitfield</div>
      <div class="person__title">Manager</div>
    </div>
    <span class="divider"></span>

    <ul class="contacts">
      <li><svg viewBox="0 0 16 16"><path d="M4 1l3 3-2 2c1 2 3 4 5 5l2-2 3 3-2 3C7 15 1 9 1 3z" fill="#fff"/></svg>555-014-2087</li>
      <li><svg viewBox="0 0 16 16"><rect x="4" y="1" width="8" height="14" rx="1.5" fill="#fff"/><rect x="5.5" y="3" width="5" height="6" fill="var(--brand-blue)"/></svg>555-019-6630</li>
      <li><svg viewBox="0 0 16 16"><rect x="1" y="3.5" width="14" height="9" fill="#fff"/><path d="M1 3.5l7 5 7-5" fill="none" stroke="var(--brand-blue)" stroke-width="1.2"/></svg>info@larkspurtalent.example</li>
      <li><svg viewBox="0 0 16 16" fill="none" stroke="#fff" stroke-width="1.2"><circle cx="8" cy="8" r="6.5"/><ellipse cx="8" cy="8" rx="3" ry="6.5"/><path d="M1.5 8h13M3 4.5h10M3 11.5h10"/></svg>www.larkspurtalent.example</li>
    </ul>
  </section>

  <section class="card card--back" aria-label="Card back">
    <div class="emblem-fade" role="img" aria-label="Large faded brand emblem"></div>

    <ul class="social">
      <li>Careerloop</li>
      <li>Blipster</li>
      <li>Myriada</li>
    </ul>

    <div class="wordmark">
      <div class="wordmark__lockup">
        <div class="wordmark__name"><span class="wordmark__dot"></span>LARKSPUR</div>
        <div class="wordmark__sub">TALENT</div>
      </div>
      <div class="wordmark__tagline">RECRUITING BRIGHT MINDS</div>
    </div>
  </section>

</main>
</body>
</html>
```